Verodex business card

Business card for sustainable investment company called "Verodex". Verodex is an exchange platform selling carbon credits between buyers and sellers. Carbon Credits are an environmental commodity for reducing global carbon emissions.

the card should obviously have our logo and the theme should be sustainability/environment mixed with a trading platform.

Contact Information for Business Card

Logo, Name, Title, Phone, Email

Colors
0054AA
0677BA
7BADD7
CADEEF
E8F1F8
0094D4
00A9DD
6FCCEA
C7EBF8
E9F6FB
00AB8E
00BBA5
67D7C9
C6EFE9
E9F9F6
59FF00
82FF00
B8FF75
E3FFCB
F4FFEA

```html
<!DOCTYPE html>
<html lang="en">
<head>
<meta charset="utf-8">
<title>Verodex business card</title>
<link rel="stylesheet" href="https://fonts.googleapis.com/css2?family=Montserrat:wght@600;700&family=Arimo:wght@400&display=swap">
<style>
  :root {
    --page: #0d0f13;
    --card: #1b2940;
    --card-light: #22344f;
    --white: #ffffff;
    --blue-deep: #0054AA;
    --blue: #0677BA;
    --cyan: #00A9DD;
    --cyan-light: #6FCCEA;
    --edge-start: #00c9e6;
    --edge-end: #1a5fe0;
  }
  * { margin: 0; padding: 0; box-sizing: border-box; }
  html, body {
    width: 1200px;
    height: 963px;
    overflow: hidden;
    background: var(--page);
  }
  .canvas {
    position: relative;
    width: 1200px;
    height: 963px;
    display: flex;
    align-items: center;
    justify-content: center;
  }
  .card-edge {
    position: relative;
    width: 960px;
    height: 552px;
    border-radius: 30px;
    padding: 0 4px 4px 0;
    background: linear-gradient(90deg, var(--edge-start), var(--edge-end));
    box-shadow: 0 30px 60px rgba(0,0,0,0.6);
  }
  .card {
    position: relative;
    width: 100%;
    height: 100%;
    border-radius: 28px;
    background: linear-gradient(135deg, var(--card) 0%, var(--card-light) 55%, var(--card) 100%);
    overflow: hidden;
  }
  .brand {
    position: absolute;
    left: 96px;
    top: 232px;
    display: flex;
    align-items: center;
    gap: 18px;
  }
  .brand-dot {
    width: 22px;
    height: 22px;
    border-radius: 50%;
    background: var(--cyan);
  }
  .brand-name {
    font-family: "Montserrat", sans-serif;
    font-weight: 700;
    font-size: 52px;
    letter-spacing: 1px;
    color: var(--white);
  }
  .divider {
    position: absolute;
    left: 470px;
    top: 140px;
    width: 1.5px;
    height: 272px;
    background: rgba(255,255,255,0.85);
  }
  .contact {
    position: absolute;
    left: 510px;
    top: 140px;
    font-family: "Arimo", sans-serif;
    color: var(--white);
  }
  .person-name {
    font-family: "Montserrat", sans-serif;
    font-weight: 700;
    font-size: 30px;
    letter-spacing: 0.5px;
    text-transform: uppercase;
    background: linear-gradient(90deg, var(--blue-deep), var(--cyan));
    -webkit-background-clip: text;
    background-clip: text;
    color: transparent;
  }
  .person-title {
    font-size: 22px;
    margin-top: 4px;
  }
  .address {
    font-size: 22px;
    line-height: 1.3;
    margin-top: 22px;
  }
  .details {
    list-style: none;
    margin-top: 22px;
  }
  .details li {
    display: flex;
    align-items: center;
    gap: 14px;
    font-size: 22px;
    line-height: 1.55;
  }
  .details svg {
    width: 20px;
    height: 20px;
    flex: none;
  }
</style>
</head>
<body>
<main class="canvas">
  <div class="card-edge">
    <section class="card">
      <div class="brand">
        <span class="brand-dot"></span>
        <span class="brand-name">VERODEX</span>
      </div>
      <div class="divider"></div>
      <div class="contact">
        <h1 class="person-name">Marcus Hale</h1>
        <p class="person-title">Manager</p>
        <p class="address">Your Address, City<br>State, Zip 0000</p>
        <ul class="details">
          <li>
            <svg viewBox="0 0 24 24" fill="none" stroke="var(--cyan)" stroke-width="2" stroke-linecap="round" stroke-linejoin="round"><path d="M5 3h4l2 5-2.5 1.5a11 11 0 0 0 6 6L16 13l5 2v4a2 2 0 0 1-2 2A16 16 0 0 1 3 5a2 2 0 0 1 2-2z"/></svg>
            555-018-4732
          </li>
          <li>
            <svg viewBox="0 0 24 24" fill="none" stroke="var(--cyan)" stroke-width="2" stroke-linejoin="round"><rect x="3" y="5" width="18" height="14" rx="1.5"/><path d="M3 6l9 7 9-7"/></svg>
            youremail@verodex.com
          </li>
          <li>
            <svg viewBox="0 0 24 24" fill="none" stroke="var(--cyan)" stroke-width="1.8"><circle cx="12" cy="12" r="9"/><ellipse cx="12" cy="12" rx="4" ry="9"/><path d="M3 12h18M5 7h14M5 17h14"/></svg>
            www.verodexhub.com
          </li>
        </ul>
      </div>
    </section>
  </div>
</main>
</body>
</html>
```